Private launch of Lulla, the smart baby sleep tracker

We need a webpage/website to initiate the Private launch of Lulla, our baby sleep tracker.

Meet Lulla:
Sleep, or rather the lack of sleep, is the one of the most challenging aspect of caring for a newborn in the first year. Recently, phone apps for baby tracking have taken hold. But those continue requiring parents to manually enter sleep and awake time. Sleep-deprived parents need a safe, automatic, accurate and stress-free tracking system. Therefore, we provide an affordable smart wearable to track baby’s sleep based on baby’s vital signs.

Target Market(s)

new parents with infants

Industry/Entity Type

Baby Care

Number of Pages Required

1 page

Font styles to use
Sans Serif

Colors
85cae6
f8ba93

Requirements
Must have
• Lulla baby sleep tracker, demonstration video, payment and ordering information. Introduction of our company "Vantor Bright Digital".
• Considering the primary targets are sleep-deprived new parents, the webpage should be user-friendly.
Nice to have
• Product rating and reviews

```html
<!DOCTYPE html>
<html lang="en">
<head>
<meta charset="utf-8">
<title>Lulla — Smart Baby Sleep Tracker | Vantor Bright Digital</title>
<link href="https://fonts.googleapis.com/css2?family=Rubik:wght@400;500;600&family=Lato:wght@400;700&display=swap" rel="stylesheet">
<style>
:root{
  --orange:#fd6a25;
  --dark:#2e3440;
  --ink:#2b2b2b;
  --text:#3a3a3a;
  --muted:#9aa0a8;
  --light:#f1f1f1;
  --green:#3bb54a;
  --red:#c8102e;
  --white:#ffffff;
}
*{margin:0;padding:0;box-sizing:border-box}
html,body{width:1200px;height:3424px;overflow:hidden}
body{position:relative;background:var(--white);font-family:'Lato',sans-serif;color:var(--text)}
.abs{position:absolute}
h1,h2,h3,.btn,.nav a,.product-name{font-family:'Rubik',sans-serif}
.btn{position:absolute;display:flex;align-items:center;justify-content:center;background:var(--orange);color:var(--white);border-radius:25px;font-size:18px;font-weight:500;height:49px;text-decoration:none}
.center{text-align:center}

/* header */
.site-header{position:absolute;left:0;top:0;width:1200px;height:95px;background:var(--white)}
.brand{position:absolute;left:74px;top:33px;display:flex;align-items:center;gap:10px;font-family:'Rubik',sans-serif;font-weight:600;font-size:23px;color:var(--ink)}
.brand-mark{width:16px;height:16px;background:var(--orange)}
.nav{position:absolute;top:43px;left:0;width:1200px;height:16px}
.nav a{position:absolute;transform:translateX(-50%);font-size:13.5px;font-weight:500;color:#333;text-decoration:none;letter-spacing:.3px;white-space:nowrap}
.nav a.active{color:var(--orange)}
.cart{position:absolute;left:1041px;top:43px;font-family:'Rubik',sans-serif;font-size:13.5px;font-weight:500;color:var(--orange);display:flex;gap:6px;align-items:center}
.cart b{color:var(--ink)}

/* hero */
.hero-photo{position:absolute;left:0;top:95px;width:1200px;height:579px;background:linear-gradient(100deg,#cfd3d8 0%,#e6e3df 35%,#bfc4cb 60%,#d9d9d9 100%)}
.hero-circle{position:absolute;left:703px;top:175px;width:420px;height:420px;border-radius:50%;background:rgba(245,245,245,.85)}
.hero-title{position:absolute;left:703px;width:420px;text-align:center;font-family:'Rubik',sans-serif;font-weight:600;line-height:1}
.hero-title.top{top:262px;font-size:48px;color:var(--orange)}
.hero-title.bottom{top:313px;font-size:52px;color:var(--ink)}
.hero-sub{position:absolute;left:733px;top:380px;width:360px;text-align:center;font-size:20px;line-height:27px;color:#333}

/* welcome */
.section-title{position:absolute;left:0;width:1200px;text-align:center;font-family:'Rubik',sans-serif;font-weight:500;font-size:32px;color:var(--ink)}
.lead{position:absolute;font-size:14px;line-height:28px;text-align:center;color:#333}

/* demo */
.demo{position:absolute;left:74px;top:1017px;width:1052px;height:396px;background:var(--dark)}
.demo h2{position:absolute;left:0;top:66px;width:568px;text-align:center;color:var(--white);font-size:32px;font-weight:500;line-height:37px}
.demo p{position:absolute;left:40px;top:154px;width:488px;text-align:center;color:#e7e9ec;font-size:14px;line-height:28px}
.video{position:absolute;left:540px;top:33px;width:484px;height:330px;background:#7d7f82;border:4px solid #a2a4a6}
.video-still{position:absolute;left:45px;top:3px;width:386px;height:316px;background:linear-gradient(135deg,#4a4645,#8b8583 45%,#5f7c79 70%,#3c3a3a)}

/* concept */
.concept{position:absolute;left:0;top:1477px;width:1200px;height:458px;background:var(--light)}
.concept-art{position:absolute;left:668px;top:61px;width:402px;height:349px;border-radius:40px;background:radial-gradient(circle at 40% 50%,#dfe9f5,#c5d6ea 60%,#f1f1f1 100%)}

/* products */
.product{position:absolute;width:300px;text-align:center}
.product-img{margin:0 auto;width:180px;height:64px;border-radius:32px}
.product-name{margin-top:35px;font-size:15px;font-weight:500;color:var(--orange);letter-spacing:.3px}
.product-age{margin-top:8px;font-size:15px;color:#333}
.product-desc{margin-top:13px;font-size:14px;color:#333}
.product-price{margin-top:17px;font-family:'Rubik',sans-serif;font-size:19px;font-weight:500;color:var(--ink)}

/* why */
.why{position:absolute;left:0;top:2386px;width:1200px;height:485px;background:#efefef}
.why-art{position:absolute;left:0;top:86px;width:365px;height:399px;background:radial-gradient(ellipse at 45% 40%,#f2c4a8,#e8a98a 45%,#efefef 75%)}
.reason{position:absolute;width:340px;height:82px}
.reason-icon{position:absolute;left:0;top:0;width:82px;height:82px;border-radius:50%;border:2px solid var(--green);display:flex;align-items:center;justify-content:center;background:transparent}
.reason.con .reason-icon{border-color:var(--red)}
.reason h3{position:absolute;left:108px;top:18px;font-size:16px;font-weight:500;color:var(--orange)}
.reason p{position:absolute;left:108px;top:44px;font-size:15px;color:#222}

/* roadmap */
.step{position:absolute;width:340px;text-align:center}
.step-icon{margin:0 auto;width:112px;height:112px;border-radius:50%;background:var(--orange);display:flex;align-items:center;justify-content:center}
.step p{margin-top:20px;font-size:16.5px;line-height:29px;color:#333}

/* footer */
.site-footer{position:absolute;left:0;top:3186px;width:1200px;height:238px;background:var(--dark);color:#d5d8dd}
.footer-brand{position:absolute;left:74px;top:80px;display:flex;align-items:center;gap:10px;font-family:'Rubik',sans-serif;font-weight:600;font-size:22px;color:var(--white)}
.copyright{position:absolute;left:74px;top:147px;font-size:11.5px;line-height:21px;color:var(--muted)}
.footer-head{position:absolute;top:38px;font-family:'Rubik',sans-serif;font-size:16px;font-weight:500;color:var(--white)}
.footer-links a{position:absolute;font-size:13px;color:#e3e5e8;text-decoration:none}
.footer-note{position:absolute;left:591px;top:71px;width:270px;font-size:13px;line-height:22px;color:#e3e5e8}
.signup{position:absolute;left:590px;top:130px;width:257px;height:38px;display:flex}
.signup-field{flex:1;background:var(--white);border-radius:19px 0 0 19px;font-size:12px;color:#666;display:flex;align-items:center;padding-left:20px}
.signup-go{width:43px;background:var(--orange);border-radius:0 19px 19px 0;display:flex;align-items:center;justify-content:center}
.social{position:absolute;left:909px;top:76px;display:flex;gap:20px}
.social span{width:22px;height:22px;border-radius:50%;background:#c9ccd1}
.pay{position:absolute;left:909px;top:142px;display:flex;gap:14px}
.pay span{width:36px;height:22px;border-radius:3px;background:#b9bdc3}
</style>
</head>
<body>

<header class="site-header">
  <div class="brand"><span class="brand-mark"></span>Vantor Bright Digital</div>
  <nav class="nav">
    <a class="active" style="left:391px">HOME</a>
    <a style="left:485px">ABOUT US</a>
    <a style="left:598px">PRODUCTS</a>
    <a style="left:709px">CONCEPT</a>
    <a style="left:812px">REVIEWS</a>
    <a style="left:928px">CONTACT US</a>
  </nav>
  <div class="cart">
    <svg width="14" height="13" viewBox="0 0 14 13"><path d="M0 1h3l2 7h7l2-5H4" fill="none" stroke="#fd6a25" stroke-width="2"/><circle cx="6" cy="11" r="1.5" fill="#fd6a25"/><circle cx="11" cy="11" r="1.5" fill="#fd6a25"/></svg>
    CART <b>(0)</b>
  </div>
</header>

<section class="hero">
  <div class="hero-photo" role="img" aria-label="Photo of a baby in a striped sailor hat sleeping on a soft white blanket"></div>
  <div class="hero-circle"></div>
  <h1 class="hero-title top">Vantor Bright</h1>
  <h1 class="hero-title bottom">Digital</h1>
  <p class="hero-sub">Nam gravida odio in commodo vestibulum vel posuere</p>
  <a class="btn" style="left:838px;top:454px;width:152px">Order Now</a>
</section>

<section class="welcome">
  <h2 class="section-title" style="top:728px">Welcome to Our Website</h2>
  <p class="lead" style="left:158px;top:789px;width:884px">Lorem ipsum dolor sit amet, consectetur adipiscing elit. Duis nibh sem, ultricies et tempus a, dictum sit amet nisi. Suspendisse dolor eros, faucibus eu gravida ac, eleifend sed odio. Cras dictum, nisl ac convallis pretium, tellus justo laoreet velit, a molestie ex sem at ligula. Nam gravida odio in commodo vestibulum.</p>
  <a class="btn" style="left:524px;top:902px;width:153px">Read More</a>
</section>

<section class="demo">
  <h2>Watch Our Product<br>Demonstration</h2>
  <p>Lorem ipsum dolor sit amet, consectetur adipiscing elit ultricies et tempus a, dictum sit amet nisi.&nbsp; Suspendisse dolor eros, faucibus eu gravida ac, eleifend sed odio.</p>
  <a class="btn" style="left:207px;top:272px;width:152px">Watch Demo</a>
  <div class="video">
    <div class="video-still" role="img" aria-label="Video still of the sleep tracker band worn on a baby's foot"></div>
    <svg class="abs" style="left:189px;top:128px" width="66" height="66" viewBox="0 0 66 66"><circle cx="33" cy="33" r="32" fill="#fff"/><path d="M25 19v28l23-14z" fill="#2b2b2b"/></svg>
  </div>
</section>

<section class="concept">
  <h2 class="section-title" style="left:0;width:690px;top:96px">Product Concept</h2>
  <p class="lead" style="left:105px;top:158px;width:480px">Lorem ipsum dolor sit amet, consectetur adipiscing elit.<br>Duis nibh sem, ultricies et tempus a, dictum sit amet nisi. dolor eros, faucibus eu gravida ac, eleifend sed odio. Cras dictum, nisl ac convallis pretium, tellus justo laoreet velit, a molestie..</p>
  <a class="btn" style="left:268px;top:302px;width:153px">Read More</a>
  <div class="concept-art" role="img" aria-label="Illustration of the tracker band and sensor linked through the cloud to a phone app showing a sleep chart, with a baby photo"></div>
</section>

<section class="products">
  <h2 class="section-title" style="top:1984px">Product</h2>
  <div class="product" style="left:90px;top:2057px">
    <div class="product-img" style="background:#e3a3ee" role="img" aria-label="Lilac sleep tracker sensor"></div>
    <div class="product-name">SLEEP TRACKER</div>
    <div class="product-age">0-1 month</div>
    <div class="product-desc">Assistant for postpartum doula</div>
    <div class="product-price">$69.00</div>
  </div>
  <div class="product" style="left:450px;top:2057px">
    <div class="product-img" style="background:#f1f1f1;box-shadow:8px 4px 0 #2b2b2b" role="img" aria-label="White sleep tracker plus sensor"></div>
    <div class="product-name">SLEEP TRACKER+</div>
    <div class="product-age">2-18 month</div>
    <div class="product-desc">First in market, Smart &amp; Affordable</div>
    <div class="product-price">$75.00</div>
  </div>
  <div class="product" style="left:810px;top:2057px">
    <div class="product-img" style="background:#8ee6a2" role="img" aria-label="Mint green sleep tracker MD sensor"></div>
    <div class="product-name">SLEEP TRACKER MD</div>
    <div class="product-age">2-18 month</div>
    <div class="product-desc">Tailored for Pediatricians</div>
    <div class="product-price">$80.00</div>
  </div>
  <a class="btn" style="left:164px;top:2298px;width:152px">Add To Cart</a>
  <a class="btn" style="left:524px;top:2298px;width:152px">Add To Cart</a>
  <a class="btn" style="left:884px;top:2298px;width:152px">Add To Cart</a>
</section>

<section class="why">
  <div class="why-art" role="img" aria-label="Photo of a hand holding the small white tracker sensor"></div>
  <h2 class="section-title" style="left:297px;width:600px;top:59px">Why Choose Lulla?</h2>

  <div class="reason" style="left:433px;top:131px">
    <div class="reason-icon"><svg width="34" height="30" viewBox="0 0 34 30"><path d="M2 2v26h30" fill="none" stroke="#3bb54a" stroke-width="2.5"/><path d="M9 12v12M14 16v8M19 8v16M24 14v10M29 10v14" stroke="#3bb54a" stroke-width="3"/></svg></div>
    <h3>Auto-tracking</h3><p>Carefree</p>
  </div>
  <div class="reason con" style="left:795px;top:131px">
    <div class="reason-icon"><svg width="38" height="28" viewBox="0 0 38 28"><rect x="6" y="3" width="26" height="17" rx="2" fill="none" stroke="#222" stroke-width="2.5"/><path d="M1 24h36" stroke="#222" stroke-width="3"/></svg></div>
    <h3>Manual Tracking</h3><p>No way</p>
  </div>
  <div class="reason" style="left:433px;top:239px">
    <div class="reason-icon"><span style="font-family:Rubik,sans-serif;font-size:34px;font-weight:500;color:#222">$</span></div>
    <h3>$68 Only</h3><p>Accurate and affordable</p>
  </div>
  <div class="reason con" style="left:795px;top:239px">
    <div class="reason-icon"><svg width="42" height="28" viewBox="0 0 42 28"><rect x="2" y="3" width="38" height="22" fill="none" stroke="#222" stroke-width="3"/><circle cx="21" cy="14" r="6" fill="#222"/><rect x="6" y="8" width="4" height="12" fill="#222"/><rect x="32" y="8" width="4" height="12" fill="#222"/></svg></div>
    <h3>$100-1000</h3><p>Trainers are expensive</p>
  </div>
  <div class="reason" style="left:433px;top:345px">
    <div class="reason-icon"><svg width="32" height="28" viewBox="0 0 32 28"><path d="M2 5h28M2 14h28M2 23h28" stroke="#222" stroke-width="2.5"/><rect x="18" y="1" width="5" height="8" fill="#222"/><rect x="8" y="10" width="5" height="8" fill="#222"/><rect x="15" y="19" width="5" height="8" fill="#222"/></svg></div>
    <h3>Flexible</h3><p>Grow with the baby</p>
  </div>
  <div class="reason con" style="left:795px;top:345px">
    <div class="reason-icon"><svg width="30" height="30" viewBox="0 0 30 30"><path d="M2 4v10l15 15 12-12L14 2H4z" fill="#222"/><circle cx="8" cy="8" r="2.5" fill="#efefef"/></svg></div>
    <h3>Fix Size</h3><p>One model fits all</p>
  </div>
</section>

<section class="roadmap">
  <div class="step" style="left:70px;top:2926px">
    <div class="step-icon"><svg width="84" height="34" viewBox="0 0 84 34"><rect x="2" y="2" width="80" height="30" rx="15" fill="#fff"/></svg></div>
    <p>Launch sleep tracker with free basic sleep training advice</p>
  </div>
  <div class="step" style="left:430px;top:2926px">
    <div class="step-icon"><svg width="46" height="46" viewBox="0 0 24 24"><path d="M6.6 10.8a15.2 15.2 0 0 0 6.6 6.6l2.2-2.2c.3-.3.7-.4 1-.2 1.1.4 2.3.6 3.6.6.6 0 1 .4 1 1V20c0 .6-.4 1-1 1A17 17 0 0 1 3 4c0-.6.4-1 1-1h3.5c.6 0 1 .4 1 1 0 1.3.2 2.5.6 3.6.1.3 0 .7-.2 1z" fill="#fff"/></svg></div>
    <p>Introduce premium paid remote sleep trainer as a service</p>
  </div>
  <div class="step" style="left:790px;top:2926px">
    <div class="step-icon"><svg width="46" height="50" viewBox="0 0 46 50"><circle cx="23" cy="13" r="10" fill="#fff"/><path d="M4 48c0-12 8-20 19-20s19 8 19 20z" fill="#fff"/><path d="M14 32v8a4 4 0 0 0 8 0" fill="none" stroke="#fd6a25" stroke-width="2.5"/><circle cx="31" cy="38" r="3" fill="none" stroke="#fd6a25" stroke-width="2.5"/></svg></div>
    <p>Integrate with pediatric hospital systems and provide advanced infant wellness care as a service</p>
  </div>
</section>

<footer class="site-footer">
  <div class="footer-brand"><span class="brand-mark"></span>Vantor Bright Digital</div>
  <div class="copyright">Copyright © 2019&nbsp; Company Name<br>All Right reserved</div>

  <div class="footer-head" style="left:330px">Quick Links</div>
  <div class="footer-links">
    <a style="left:330px;top:71px">Home</a>
    <a style="left:330px;top:102px">About Us</a>
    <a style="left:330px;top:134px">Products</a>
    <a style="left:330px;top:165px">Concept</a>
    <a style="left:467px;top:71px">Reviews</a>
    <a style="left:467px;top:102px">Contact Us</a>
  </div>

  <div class="footer-head" style="left:591px">Email Sign Up</div>
  <p class="footer-note">Lorem ipsum dolor sit amet, consectetur adipiscing venenatis est..</p>
  <div class="signup">
    <div class="signup-field">Enter Email Address</div>
    <div class="signup-go"><svg width="12" height="16" viewBox="0 0 12 16"><path d="M3 2l6 6-6 6" fill="none" stroke="#fff" stroke-width="3"/></svg></div>
  </div>

  <div class="footer-head" style="left:909px">Follow Us</div>
  <div class="social"><span></span><span></span><span></span><span></span><span></span></div>
  <div class="pay"><span></span><span></span><span></span><span></span></div>
</footer>

</body>
</html>
```